Real Estate Card Design

I need a new business card! Below you will find my headshot, the company logo and a copy of my previous business card.

The card must contain the following information:

Dana Wexley
Sales Representative
FERNBROOK HOMES REALTY INC BROKERGE
204-517 Marsh Rd E, Oshawa ON L1H 4K7
Cell: 905-618-3074 Office:905-481-2696
www.danawexley.example dana@homesbywexley.example

I would like the card to portray security and class all the while being fresh and contemporary. I hold the key....

```html
<!DOCTYPE html>
<html lang="en">
<head>
<meta charset="utf-8">
<title>Dana Wexley — Business Card</title>
<link href="https://fonts.googleapis.com/css2?family=Josefin+Sans:wght@400;700&family=Source+Sans+3:wght@400;600&display=swap" rel="stylesheet">
<style>
  :root {
    --page: #e9e9ea;
    --card-top: #fbfbfb;
    --card-mid: #eeeeef;
    --card-low: #cfd0d2;
    --ink: #1b1b1d;
    --ink-soft: #333336;
    --accent: #1f9ad6;
    --logo-blue: #3aa7df;
    --photo-dark: #1f2634;
    --photo-mid: #3a4150;
  }
  * { box-sizing: border-box; margin: 0; padding: 0; }
  html, body { width: 1200px; height: 900px; overflow: hidden; }
  body {
    background: var(--page);
    font-family: "Source Sans 3", sans-serif;
    position: relative;
  }
  .card {
    position: absolute;
    left: 50px; top: 135px;
    width: 1100px; height: 630px;
    background: linear-gradient(172deg, var(--card-top) 0%, var(--card-mid) 55%, var(--card-low) 100%);
    box-shadow: 0 18px 40px rgba(0,0,0,0.18), 0 2px 6px rgba(0,0,0,0.12);
    overflow: hidden;
  }
  .brand {
    position: absolute;
    left: 58px; top: 42px;
    display: flex; align-items: center; gap: 14px;
  }
  .brand-square {
    width: 60px; height: 60px;
    background: var(--logo-blue);
  }
  .brand-name {
    font-family: "Josefin Sans", sans-serif;
    font-weight: 400;
    font-size: 22px;
    line-height: 1.15;
    letter-spacing: 1px;
    color: var(--ink);
    text-transform: uppercase;
  }
  .identity {
    position: absolute;
    left: 58px; top: 250px;
  }
  .identity-name {
    font-family: "Josefin Sans", sans-serif;
    font-size: 58px;
    line-height: 1;
    letter-spacing: 1px;
    color: var(--ink);
    text-transform: uppercase;
    white-space: nowrap;
  }
  .identity-name .first { font-weight: 700; }
  .identity-name .last { font-weight: 400; }
  .identity-role {
    display: inline-block;
    margin-top: 10px;
    font-size: 22px;
    color: var(--ink-soft);
    padding-bottom: 5px;
    border-bottom: 3px solid var(--accent);
  }
  .contacts {
    position: absolute;
    left: 46px; top: 440px;
    list-style: none;
  }
  .contact {
    display: flex; align-items: center; gap: 12px;
    height: 34px;
    font-size: 20px;
    color: var(--ink-soft);
    white-space: nowrap;
  }
  .contact-icon { width: 24px; height: 24px; flex: none; }
  .contact--office { font-size: 15px; text-transform: uppercase; margin-top: 4px; }
  .contact-address {
    padding-left: 36px;
    font-size: 12px;
    color: var(--ink-soft);
    margin-top: -6px;
  }
  .portrait {
    position: absolute;
    right: 0; top: 0;
    width: 460px; height: 630px;
    background: linear-gradient(180deg, var(--photo-mid) 0%, var(--photo-dark) 100%);
  }
</style>
</head>
<body>
  <main class="card">
    <div class="brand">
      <div class="brand-square"></div>
      <div class="brand-name">Fernbrook Homes<br>Realty Inc.</div>
    </div>

    <section class="identity">
      <h1 class="identity-name"><span class="first">Dana</span><span class="last">Wexley</span></h1>
      <p class="identity-role">Sales Representative</p>
    </section>

    <ul class="contacts">
      <li class="contact">
        <svg class="contact-icon" viewBox="0 0 24 24"><circle cx="12" cy="12" r="12" fill="var(--accent)"/><path d="M8.5 6.5l2 2.2-1.2 1.6c.8 1.8 2.2 3.2 4 4l1.6-1.2 2.2 2-1.3 1.8c-4.5-.4-8.7-4.6-9.1-9.1z" fill="#fff"/></svg>
        <span>905-618-3074 &nbsp;:905-481-2696</span>
      </li>
      <li class="contact">
        <svg class="contact-icon" viewBox="0 0 24 24"><circle cx="12" cy="12" r="12" fill="var(--accent)"/><rect x="6.5" y="8" width="11" height="8" fill="#fff"/><path d="M6.5 8l5.5 4.5L17.5 8" fill="none" stroke="var(--accent)" stroke-width="1.2"/></svg>
        <span>dana@homesbywexley.example</span>
      </li>
      <li class="contact">
        <svg class="contact-icon" viewBox="0 0 24 24"><circle cx="12" cy="12" r="12" fill="var(--accent)"/><path d="M8.5 6l8 6.5-3.6.4 2 4.2-1.6.8-2-4.2-2.8 2.4z" fill="#fff"/></svg>
        <span>www.danawexley.example</span>
      </li>
      <li class="contact contact--office">
        <svg class="contact-icon" viewBox="0 0 24 24"><circle cx="12" cy="12" r="12" fill="var(--accent)"/><path d="M8.5 6.5l2 2.2-1.2 1.6c.8 1.8 2.2 3.2 4 4l1.6-1.2 2.2 2-1.3 1.8c-4.5-.4-8.7-4.6-9.1-9.1z" fill="#fff"/></svg>
        <span>FERNBROOK HOMES REALTY INC BROKERGE</span>
      </li>
      <li class="contact-address">204-517 Marsh Rd E, Oshawa ON L1H 4K7</li>
    </ul>

    <div class="portrait" role="img" aria-label="Headshot of the sales representative in a dark pinstripe suit holding up a house key"></div>
  </main>
</body>
</html>
```